Business Card Design - Amberfield Court

We are looking at a new design for our business cards that has a modern and professional look. We run a residential aged care facility focussing on the care of residents. The cards will be used for potential clients, consultants and business opportunities in this sector. Blue and white is our main colours and would to see these colours incorporated in the design.
Industry/Entity Type
Business
Contact Information for Business Card
Amberfield Court, Darren Walsh, dwalsh@amberfieldcourt.com.au, Finance Manager, 0472 639 208, BCom, 37 Marrabel Crescent, Brindle Vale, Qld 4093.
Look and feel
Each slider illustrates characteristics of the customer's brand and the style your logo design should communicate.

```html
<!DOCTYPE html>
<html lang="en">
<head>
<meta charset="utf-8">
<title>Amberfield Court – Business Card</title>
<link href="https://fonts.googleapis.com/css2?family=Oswald:wght@300;400&family=Arimo:ital,wght@0,400;0,700;1,400&display=swap" rel="stylesheet">
<style>
  :root {
    --page-bg: #e9ecee;
    --brand-blue: #4a7d97;
    --brand-blue-deep: #3f6f88;
    --brand-blue-light: #8db2c4;
    --card-white: #ffffff;
    --card-silver: #e4e6e8;
    --text-light: #ffffff;
    --shadow: rgba(30, 45, 55, 0.22);
  }
  * { margin: 0; padding: 0; box-sizing: border-box; }
  html, body {
    width: 1200px;
    height: 950px;
    overflow: hidden;
    background: var(--page-bg);
  }
  .canvas {
    width: 1200px;
    height: 950px;
    display: flex;
    flex-direction: column;
    align-items: center;
    justify-content: center;
    gap: 48px;
  }
  .card {
    position: relative;
    width: 720px;
    height: 411px;
    overflow: hidden;
    box-shadow: 0 10px 28px var(--shadow);
  }

  /* Front */
  .card-front {
    background: linear-gradient(115deg, var(--brand-blue-deep) 0%, var(--brand-blue) 45%, var(--brand-blue-light) 100%);
    color: var(--text-light);
  }
  .front-glow {
    position: absolute;
    right: -60px;
    bottom: -120px;
    width: 520px;
    height: 400px;
    border-radius: 50%;
    background: radial-gradient(ellipse at 55% 55%, rgba(255,255,255,0.95) 0%, rgba(255,255,255,0.75) 40%, rgba(255,255,255,0) 72%);
  }
  .brand-name {
    position: absolute;
    left: 36px;
    top: 30px;
    font-family: "Oswald", sans-serif;
    font-weight: 300;
    font-size: 31px;
    letter-spacing: 0.14em;
    text-transform: uppercase;
    line-height: 1;
  }
  .tagline {
    position: absolute;
    left: 36px;
    top: 72px;
    font-family: "Arimo", sans-serif;
    font-style: italic;
    font-size: 19px;
    letter-spacing: 0.02em;
  }
  .contact {
    position: absolute;
    left: 36px;
    top: 150px;
    font-family: "Arimo", sans-serif;
    font-size: 17px;
    line-height: 1.32;
  }
  .contact .person {
    font-weight: 700;
    font-size: 20px;
    text-transform: uppercase;
    letter-spacing: 0.02em;
  }
  .contact .person .credential { font-size: 17px; }
  .contact .role {
    text-transform: uppercase;
    margin-bottom: 6px;
  }
  .contact .gap { margin-top: 6px; }

  /* Back */
  .card-back {
    background: linear-gradient(120deg, var(--card-white) 0%, var(--card-white) 40%, var(--card-silver) 100%);
    display: flex;
    align-items: center;
    justify-content: center;
  }
  .back-mark {
    display: flex;
    align-items: center;
    gap: 18px;
  }
  .back-mark .dot {
    width: 56px;
    height: 56px;
    border-radius: 50%;
    background: var(--brand-blue);
  }
  .back-mark .name {
    font-family: "Oswald", sans-serif;
    font-weight: 300;
    font-size: 40px;
    letter-spacing: 0.14em;
    text-transform: uppercase;
    color: var(--brand-blue);
  }
</style>
</head>
<body>
  <main class="canvas">
    <section class="card card-front">
      <div class="front-glow" role="img" aria-label="Soft white brand decoration area"></div>
      <h1 class="brand-name">Amberfield Court</h1>
      <p class="tagline">Comfort, Respect and Belonging</p>
      <div class="contact">
        <p class="person">Darren Walsh <span class="credential">BCom</span></p>
        <p class="role">Finance Manager</p>
        <p class="gap">37 Marrabel Crescent</p>
        <p>Brindle Vale, Qld 4093.</p>
        <p class="gap">0472 639 208</p>
        <p>dwalsh@amberfieldcourt.com.au</p>
        <p>www.amberfieldcourt.com.au</p>
      </div>
    </section>

    <section class="card card-back">
      <div class="back-mark">
        <span class="dot"></span>
        <span class="name">Amberfield Court</span>
      </div>
    </section>
  </main>
</body>
</html>
```